Mortgage and Asset Finance Broker Needs a Wordpress Website Design

I need a modern looking Wordpress website to showcase my service as a mortgage and asset broker. I have a company and we work with various lenders to arrange mortgages, as well as commercial lending and business asset finance. The website needs to look professional, be easy to navigate and capture leads. SEO is obviously very important to me. It really needs to be something that shows trust and professioanlism.
Updates

On the home page I will need to have some boxes for Home Loans, Refinancing, Business (and Agriculture) Loans etc. I'd like a carousel in the middle which shows our lenders (so that can have the banks logos added).

It needs to be easy top navigate and showcase all we do - Home Loans, Refinancing, Commercial Loans, Car Loans, Asset Finance etc.

There are plenty of companies on the internet that do this.

There is some good information here https://lendplatehq.com.au/mortgage-broker-homepage/

I need to make sure that editing the website is easy (I think Wordpress has something that allows that).

Also we are very much an Australian business so that is something to advertise.

Industry/Entity Type

Mortgage and Finance Broker

Coding

Coded - Design and coding required

Number of Pages Required

5+ page

Requirements
Must have
• Easy to navigate professional feel. Must be responsive and mobile friendly.
Nice to have
• Homepage with links to inner pages. Contact buttons.

```html
<!DOCTYPE html>
<html lang="en">
<head>
<meta charset="utf-8">
<title>Harbourline Financial Services</title>
<link rel="stylesheet" href="https://fonts.googleapis.com/css2?family=Barlow:wght@500;600&family=Lato:ital,wght@0,400;0,700;1,400&display=swap">
<style>
:root{
  --blue:#1d4f9c;
  --pink:#e1245f;
  --ink:#1d1d1f;
  --muted:#555;
  --grad:linear-gradient(90deg,#7d2a8c,#2449a6);
  --soft-blue:#dde9f7;
  --soft-pink:#fbdde7;
  --soft-lilac:#f2d5f2;
  --soft-peach:#fbe9d8;
}
*{box-sizing:border-box;margin:0;padding:0}
html,body{width:1200px;height:3079px;overflow:hidden;background:#fff}
body{font-family:"Lato",sans-serif;color:var(--ink);position:relative}
.h{font-family:"Barlow",sans-serif;font-weight:600}
.b{color:var(--blue)} .p{color:var(--pink)}
.abs{position:absolute}
.btn{position:absolute;background:var(--grad);color:#fff;font-family:"Barlow",sans-serif;font-weight:600;font-size:19px;display:flex;align-items:center;justify-content:center;border-radius:10px 0 10px 0}
/* header */
.topbar{position:absolute;left:680px;top:0;width:520px;height:33px;background:var(--pink);clip-path:polygon(24px 0,100% 0,100% 100%,0 100%);color:#fff;font-family:"Barlow",sans-serif;font-size:18px;font-weight:500}
.brand{position:absolute;left:92px;top:24px;font-family:"Barlow",sans-serif;font-weight:600;font-size:38px;color:var(--ink);display:flex;align-items:center;gap:10px}
.brand i{display:block;width:26px;height:26px;background:var(--pink)}
.brand small{display:block;font-size:12px;letter-spacing:1px;font-weight:500}
.nav{position:absolute;left:352px;top:57px;display:flex;gap:30px;font-size:16px;color:#333}
.nav .on{color:var(--blue)}
/* hero */
.hero{position:absolute;left:0;top:108px;width:1200px;height:515px;background:linear-gradient(90deg,#f3efea 0%,#ece5dc 45%,#d9cfc4 100%)}
.hero-photo{position:absolute;right:0;top:0;width:560px;height:515px;background:linear-gradient(160deg,#e7e0d8,#c7b49c 60%,#b59a7b)}
/* intro */
.strip{position:absolute;top:0;border-radius:14px;background:linear-gradient(180deg,#6b4a36,#c9b29a)}
/* services */
.services{position:absolute;left:0;top:1188px;width:1200px;height:590px;background:var(--soft-pink)}
.card{position:absolute;top:1364px;width:298px;height:244px;background:linear-gradient(135deg,#c9b69c,#8f7b66);clip-path:polygon(0 0,100% 25%,100% 100%,0 100%);border-radius:14px}
.card-label{position:absolute;top:1630px;width:298px;text-align:center;font-size:26px}
.arrow{position:absolute;width:20px;height:20px;border:1.5px solid #333;border-radius:50%;font-size:12px;display:flex;align-items:center;justify-content:center}
/* partners */
.partner{position:absolute;top:1942px;width:172px;height:106px;background:#fff;box-shadow:0 3px 10px rgba(0,0,0,.12);border-radius:4px;display:flex;align-items:center;justify-content:center}
.partner span{width:70px;height:46px;border-radius:6px;background:#c8d3e6}
.pname{position:absolute;top:2070px;width:172px;text-align:center;font-size:16px}
/* testimonials */
.testi{position:absolute;left:0;top:2178px;width:1200px;height:502px;background:var(--soft-peach)}
.tcard{position:absolute;top:2352px;width:388px;height:220px;background:#fff;border-radius:12px;box-shadow:0 4px 14px rgba(0,0,0,.1);padding:28px 30px 0 68px;font-size:14.5px;line-height:26px}
.tcard em{color:#666}
.avatar{position:absolute;top:2418px;width:88px;height:88px;border-radius:50%}
.quote{position:absolute;top:2330px;font-family:Georgia,serif;font-size:60px;color:#e98aa6;line-height:1}
/* footer */
.fcol h4{font-family:"Barlow",sans-serif;font-weight:500;font-size:23px;margin-bottom:8px}
.fcol li{list-style:none;font-size:15px;line-height:29px;padding-left:24px;position:relative}
.fcol.dots li:before{content:"";position:absolute;left:0;top:11px;width:8px;height:8px;border-radius:50%;background:var(--pink)}
</style>
</head>
<body>

<!-- Header -->
<div class="topbar">
  <svg class="abs" style="left:60px;top:8px" width="16" height="16" viewBox="0 0 24 24"><path fill="#fff" d="M6.6 10.8a15 15 0 006.6 6.6l2.2-2.2c.3-.3.7-.4 1-.2 1.1.4 2.3.6 3.6.6.6 0 1 .4 1 1V20c0 .6-.4 1-1 1A17 17 0 013 4c0-.6.4-1 1-1h3.5c.6 0 1 .4 1 1 0 1.3.2 2.5.6 3.6.1.3 0 .7-.2 1z"/></svg>
  <span class="abs" style="left:92px;top:6px">1300 555 018</span>
  <span class="abs" style="left:286px;top:10px;display:flex;gap:18px">
    <i style="width:14px;height:14px;border:2px solid #fff;border-radius:50%"></i>
    <i style="width:14px;height:14px;border:2px solid #fff;border-radius:50%"></i>
    <i style="width:14px;height:14px;border:2px solid #fff;border-radius:50%"></i>
    <i style="width:14px;height:14px;border:2px solid #fff;border-radius:50%"></i>
  </span>
</div>
<div class="brand"><i></i><div>Harbourline<small>FINANCIAL SERVICES</small></div></div>
<nav class="nav"><span class="on">Home</span><span>About Us</span><span>Services</span><span>Lenders</span><span>Resources</span><span>Testimonials</span></nav>
<div class="btn" style="left:936px;top:47px;width:158px;height:47px">Contact Us</div>

<!-- Hero -->
<section class="hero">
  <div class="hero-photo" role="img" aria-label="Family of three sitting on moving boxes in front of a brick wall"></div>
  <h1 class="h abs" style="left:108px;top:118px;font-size:60px"><span class="b">Direct &amp;</span> <span class="p">Professional</span></h1>
  <p class="abs" style="left:108px;top:210px;font-size:15px;line-height:31px">Your Trusted Partner for Home Loans, Business Loans, and Asset Finance<br>Helping You Secure the Best Rates and Terms with Leading Lenders.</p>
  <div class="btn" style="left:111px;top:310px;width:184px;height:47px">Get Started</div>
</section>

<!-- Company introduction -->
<section class="abs" style="left:0;top:708px;width:1200px;height:390px">
  <div class="strip" style="left:91px;top:50px;width:14px;height:286px;background:#333"></div>
  <div class="strip" style="left:112px;top:22px;width:18px;height:348px"></div>
  <div class="strip" style="left:137px;top:0;width:28px;height:388px"></div>
  <div class="abs" role="img" aria-label="Advisor meeting a client at a desk with laptop and documents" style="left:171px;top:0;width:388px;height:388px;border-radius:16px;background:linear-gradient(135deg,#e9e4dc,#b8a48e)"></div>
  <h2 class="h abs" style="left:643px;top:26px;font-size:44px"><span class="b">Company</span> <span class="p">Introduction</span></h2>
  <p class="abs" style="left:643px;top:100px;width:450px;font-size:15px;line-height:26px">We are a team of dedicated mortgage and asset finance professionals with a passion for helping individuals and businesses achieve their financial goals. With years of experience in the industry, we specialize in providing customized loan solutions that meet your unique needs. Whether you're buying your first home, refinancing, or looking for business financing, we are here to guide you through the process.</p>
  <div class="btn" style="left:643px;top:304px;width:183px;height:47px">Get Started</div>
</section>

<!-- Services -->
<section class="services">
  <svg class="abs" style="left:0;top:0" width="1200" height="590"><polygon points="0,20 1200,590 0,590" fill="#dde9f7"/></svg>
</section>
<h2 class="h abs" style="left:0;top:1268px;width:1200px;text-align:center;font-size:44px"><span class="b">Our</span> <span class="p">Services</span></h2>
<div class="arrow" style="left:44px;top:1498px">&larr;</div>
<div class="arrow" style="left:1132px;top:1498px">&rarr;</div>
<div class="card" style="left:111px" role="img" aria-label="Hand holding house keys beside a small wooden house model"></div>
<div class="card" style="left:450px;border:2px solid var(--pink);background:linear-gradient(135deg,#eef0f3,#b9bfc8)" role="img" aria-label="Hands signing loan documents next to a calculator"></div>
<div class="card" style="left:790px;background:linear-gradient(135deg,#f0f0f0,#9ea7b3)" role="img" aria-label="Person signing a car loan agreement beside a toy car"></div>
<div class="card-label h" style="left:105px;font-weight:500">Home Loans</div>
<div class="card-label h b" style="left:443px;font-weight:500">Commercial Loans</div>
<div class="card-label h" style="left:785px;font-weight:500">Car Loans</div>

<!-- Lending partners -->
<h2 class="h abs" style="left:0;top:1848px;width:1200px;text-align:center;font-size:44px"><span class="b">Our Trusted</span> <span class="p">Lending Partners</span></h2>
<div class="arrow" style="left:59px;top:1987px">&larr;</div>
<div class="arrow" style="left:1131px;top:1987px">&rarr;</div>
<div class="partner" style="left:111px"><span></span></div>
<div class="partner" style="left:312px"><span></span></div>
<div class="partner" style="left:514px"><span></span></div>
<div class="partner" style="left:714px"><span></span></div>
<div class="partner" style="left:916px"><span></span></div>
<div class="pname" style="left:111px">Coastal Bank</div>
<div class="pname" style="left:312px">Southern Mutual</div>
<div class="pname" style="left:514px">Meridian Bank</div>
<div class="pname" style="left:714px">Ridgeway Bank</div>
<div class="pname" style="left:916px">Eastbrook Bank</div>

<!-- Testimonials -->
<section class="testi">
  <svg class="abs" style="left:0;top:0" width="1200" height="502"><polygon points="0,0 1200,0 0,502" fill="#f2d5f2"/></svg>
</section>
<h2 class="h abs" style="left:0;top:2256px;width:1200px;text-align:center;font-size:44px"><span class="b">What Our Clients</span> <span class="p">Say About Us</span></h2>
<svg class="abs" style="left:52px;top:2452px" width="14" height="22"><path d="M11 2L3 11l8 9" fill="none" stroke="#333" stroke-width="2"/></svg>
<svg class="abs" style="left:1140px;top:2452px" width="14" height="22"><path d="M3 2l8 9-8 9" fill="none" stroke="#333" stroke-width="2"/></svg>
<div class="tcard" style="left:171px"><em>I was a first-time homebuyer and honestly felt overwhelmed by the process. The team at [Your Company Name] helped me understand my options and guided me through every step. They found me a great</em><br>Emily<br><span style="color:#666">Homeowner</span></div>
<div class="tcard" style="left:702px"><em>As a small business owner, securing a loan was essential to expand my operations. [Your Company Name] took the time to understand my needs and connected me with a lender who offered the perfect</em><br>John<br><span style="color:#666">Business Owner</span></div>
<div class="quote" style="left:242px">&ldquo;</div>
<div class="quote" style="left:772px">&ldquo;</div>
<div class="avatar" style="left:112px;background:#e88a8f" role="img" aria-label="Portrait of Emily"></div>
<div class="avatar" style="left:642px;background:#c9d4e2" role="img" aria-label="Portrait of John"></div>

<!-- Footer -->
<div class="brand" style="left:110px;top:2770px;font-size:44px"><i style="width:30px;height:30px"></i><div>Harbourline<small style="font-size:14px">FINANCIAL SERVICES</small></div></div>
<div class="abs" style="left:143px;top:2906px;display:flex;gap:20px">
  <i style="width:20px;height:20px;border-radius:50%;background:var(--blue)"></i>
  <i style="width:20px;height:20px;border-radius:50%;background:var(--blue)"></i>
  <i style="width:20px;height:20px;border-radius:50%;background:var(--blue)"></i>
</div>
<div class="fcol dots abs" style="left:466px;top:2790px"><h4>Quick Links</h4><ul><li>Home</li><li>About Us</li><li>Services</li><li>Lenders</li><li>Resources</li><li>Testimonials</li></ul></div>
<div class="fcol dots abs" style="left:672px;top:2790px"><h4>Legal Information</h4><ul><li>Privacy Policy</li><li>Terms &amp; Conditions</li><li>Disclaimer</li></ul></div>
<div class="fcol abs" style="left:914px;top:2790px"><h4>Contact us</h4><ul>
  <li><svg class="abs" style="left:-2px;top:6px" width="18" height="18"><circle cx="9" cy="9" r="8" fill="none" stroke="var(--pink)" stroke-width="1.5"/></svg>1300 555 018</li>
  <li><svg class="abs" style="left:-2px;top:6px" width="18" height="18"><path d="M9 16s6-5 6-9a6 6 0 00-12 0c0 4 6 9 6 9z" fill="none" stroke="var(--pink)" stroke-width="1.5"/></svg>45 Harbour Street</li>
  <li>Sydney NSW 2000</li><li>Australia</li>
  <li><svg class="abs" style="left:-2px;top:6px" width="18" height="18"><circle cx="9" cy="9" r="8" fill="var(--pink)"/></svg>info@harbourline.com</li></ul></div>
<div class="abs" style="left:0;top:3023px;width:1200px;height:1px;background:#ccc"></div>
<p class="abs" style="left:0;top:3037px;width:1200px;text-align:center;font-size:15px">Copyright © 2025 Harbourline Finance Services. All rights reserved.</p>
</body>
</html>
```